Harbourline Electrical Solutions

On one side. LOGO (underneath:) Commercial Industrial Residential

- NAME & CONTACT DETAILS

Marcus T. Hollings
Project Manager

(Cell icon) (441) 555-0187
(Email icon) hlelectricalsolutions@mailvento.com
(Facebook & Instagram icons )@hlelectricalsolutions

Other side: LOGO - underneath ELECTRICAL CONSTRUCTION & MAINTENANCE . LED LIGHTING & AUTOMATION . LIFE SAFETY SYSTEMS (FIRE ALARM / SECURITY) . DATA & COMMUNICATION

```html
<!DOCTYPE html>
<html lang="en">
<head>
<meta charset="utf-8">
<title>Harbourline Electrical Solutions – Business Card</title>
<link href="https://fonts.googleapis.com/css2?family=Montserrat:wght@400;500;600&family=Roboto:wght@400;500&family=Exo+2:ital,wght@1,700&display=swap" rel="stylesheet">
<style>
  :root {
    --backdrop: #3a3a3c;
    --card-black: #111214;
    --panel-black: #0b0c0e;
    --brand-blue: #0f5a76;
    --accent-blue: #1e8fd6;
    --edge-grey: #4a4d52;
    --text-white: #ffffff;
    --text-silver: #b9bcc2;
  }
  * { box-sizing: border-box; margin: 0; padding: 0; }
  html, body {
    width: 799px; height: 1200px; overflow: hidden;
    background: var(--backdrop);
  }
  .canvas {
    position: relative; width: 799px; height: 1200px;
  }
  .card {
    position: absolute; left: 80px; width: 640px; height: 366px;
    overflow: hidden; color: var(--text-white);
    box-shadow: 0 14px 30px rgba(0,0,0,.45);
  }
  .card--front { top: 150px; background: var(--card-black); }
  .card--back { top: 680px; background: var(--brand-blue); }

  /* Front */
  .front-brand {
    position: absolute; top: 60px; right: 44px; width: 330px;
    display: flex; align-items: center; gap: 16px;
    font-family: "Montserrat", sans-serif; font-weight: 500;
    color: var(--text-silver); text-transform: uppercase;
    letter-spacing: 4px; font-size: 22px; line-height: 1.15;
  }
  .brand-square {
    flex: none; width: 46px; height: 46px; background: var(--edge-grey);
  }
  .services {
    position: absolute; left: 44px; top: 186px; width: 560px;
    font-family: "Montserrat", sans-serif; font-size: 14.5px; line-height: 1.5;
  }
  .accent-rule {
    position: absolute; left: 44px; right: 36px; top: 250px;
    height: 2px; background: var(--accent-blue);
  }
  .sectors {
    position: absolute; left: 44px; top: 280px;
    font-family: "Montserrat", sans-serif; font-weight: 600;
    font-size: 15px; letter-spacing: 3px; word-spacing: 8px;
  }

  /* Back */
  .back-panel { position: absolute; inset: 0; }
  .back-brand {
    position: absolute; left: 34px; top: 100px; width: 210px;
    font-family: "Montserrat", sans-serif; font-weight: 600;
    font-size: 21px; line-height: 1.15; letter-spacing: 2px;
    text-transform: uppercase; color: var(--text-white);
  }
  .back-sectors {
    position: absolute; left: 34px; top: 212px;
    font-family: "Montserrat", sans-serif; font-weight: 500;
    font-size: 8.5px; letter-spacing: 1px; color: var(--text-white);
  }
  .person {
    position: absolute; left: 330px; top: 118px;
  }
  .person__name {
    font-family: "Exo 2", sans-serif; font-style: italic; font-weight: 700;
    font-size: 23px;
  }
  .person__role {
    font-family: "Roboto", sans-serif; font-size: 14px; margin-top: 2px;
  }
  .contacts {
    position: absolute; left: 300px; top: 196px; list-style: none;
    font-family: "Roboto", sans-serif; font-size: 14.5px; line-height: 1.45;
  }
  .contacts li { display: flex; align-items: center; gap: 9px; }
  .contacts svg { flex: none; width: 13px; height: 13px; }
  .social-dot {
    flex: none; width: 13px; height: 13px; border-radius: 50%;
    background: var(--text-white);
  }
</style>
</head>
<body>
<main class="canvas">

  <section class="card card--front" aria-label="Card front">
    <div class="front-brand">
      <span class="brand-square" aria-hidden="true"></span>
      <span>Harbourline Electrical Solutions</span>
    </div>
    <p class="services">
      Electrical Construction &amp; Maintenance | Led Lighting &amp; Automation<br>
      Life Safety Systems (Fire Alarm/Security) | Data &amp; Communication
    </p>
    <div class="accent-rule"></div>
    <p class="sectors">COMMERCIAL | INDUSTRIAL | RESIDENTIAL</p>
  </section>

  <section class="card card--back" aria-label="Card back">
    <svg class="back-panel" viewBox="0 0 640 366" aria-hidden="true">
      <path d="M0 0 H300 C262 120 205 270 160 366 H0 Z" fill="var(--edge-grey)"/>
      <path d="M0 0 H290 C252 120 195 270 150 366 H0 Z" fill="var(--panel-black)"/>
    </svg>
    <div class="back-brand">Harbourline Electrical Solutions</div>
    <p class="back-sectors">COMMERCIAL | INDUSTRIAL | RESIDENTIAL</p>

    <div class="person">
      <p class="person__name">Marcus T. Hollings</p>
      <p class="person__role">Project Manager</p>
    </div>
    <ul class="contacts">
      <li>
        <svg viewBox="0 0 16 16" aria-hidden="true"><path fill="#fff" d="M3 2 h3 l1 3 -2 1.5 a8 8 0 0 0 4.5 4.5 L11 9 l3 1 v3 a1 1 0 0 1 -1 1 A11 11 0 0 1 2 3 a1 1 0 0 1 1 -1z"/></svg>
        (441) 555-0187
      </li>
      <li>
        <svg viewBox="0 0 16 16" aria-hidden="true"><rect x="1" y="3" width="14" height="10" fill="#fff"/><path d="M1 3 L8 9 L15 3" fill="none" stroke="#0f5a76" stroke-width="1.3"/></svg>
        hlelectricalsolutions@mailvento.com
      </li>
      <li><span class="social-dot" aria-hidden="true"></span>@hlelectricalsolutions</li>
      <li><span class="social-dot" aria-hidden="true"></span>@hlelectricalsolutions</li>
    </ul>
  </section>

</main>
</body>
</html>
```